Brimora - Nutritious Snacks and Desserts

We need a creative e-commerce website in which all features--buttons, background, etc.--convey our message: We sell delicious, nutritious snacks and desserts that most closely comply with the paleo diet guidelines. Our first product is Nuttaree®--raw, vegan, paleo chocolate balls that are made of dates, coconut, and cocoa. Our products are organic, raw, irresistible and nutritious. We have several versions of Nuttaree® in development, as well as mousse, ice cream, and crackers. Our mission is to purvey basic healthy foods. Our motto is, "Fuel for the Bold Trail-Walker(tm)."

Target Market(s)

Health-conscious professionals who tend to shop at health food stores. Our products also meet the requirements of a gluten-free diet; and they also don't contain refined sugar, so shoppers with gluten and possibly sugar issues are incidental customers.

Industry/Entity Type

Health Product

Coding

Number of Pages Required

5+ page

Colors

Designer to choose colors to be used in the design.

Requirements
Must have
• We need at least a home page, a products page, an about-us page, a contact page, and a shopping cart page. We would like to be able to add products on our own later. We should be able to handle some basic coding, especially if it's just a matter of copying and modifying product pages. We would also like the ability in the future to add blogging pages, allowing us to write articles about health food and healthy lifestyle, thus attracting web-traffic (SEO).
• Other features we would like to have:
• Product photo slider on the hopepage
• Back-to-top button at the bottom of the home page
• Make sure the site is mobile-compatible
• A search bar at the top of the homepage
• "Create an account" and "Previous orders"--allowing customers to see their previous orders and reorder what they purchased in the past.
Nice to have
• We would like to convey the paleo theme without actually stating it anywhere. We'll add text as necessary, according to the page layout; you can use ipsum lorem for purpose of demonstration.

```html
<!DOCTYPE html>
<html lang="en">
<head>
<meta charset="utf-8">
<title>Brimora - Nutritious Snacks and Desserts</title>
<link href="https://fonts.googleapis.com/css2?family=Montserrat:wght@400;500;600;700&family=Open+Sans:wght@400;600&display=swap" rel="stylesheet">
<style>
:root{
  --green:#8cc63f;
  --green-dark:#6fae24;
  --text:#444;
  --muted:#777;
  --light:#f2f4f6;
  --line:#e3e6e9;
  --wood:#2b2b2b;
  --wood-dark:#1d1d1d;
  --foot-text:#e6e6e6;
  --white:#fff;
}
*{margin:0;padding:0;box-sizing:border-box}
html,body{width:1200px;height:2490px;overflow:hidden;background:var(--white)}
body{position:relative;font-family:"Open Sans",Arial,sans-serif;color:var(--text)}
.abs{position:absolute}

/* header */
.site-header{left:0;top:0;width:1200px;height:127px;background:var(--white);border-top:4px solid var(--green)}
.call-tab{left:840px;top:0;width:270px;height:45px}
.call-tab span{position:absolute;left:0;top:0;width:100%;line-height:45px;text-align:center;color:var(--white);font:600 15px "Montserrat",sans-serif;letter-spacing:.5px}
.brand{left:85px;top:14px;width:130px;text-align:center}
.brand-mark{display:block;margin:0 auto;width:56px;height:56px;border-radius:50%;background:var(--green)}
.brand-name{display:block;margin-top:6px;font:600 30px "Montserrat",sans-serif;color:var(--green);letter-spacing:1px}
.main-nav{left:357px;top:84px;display:flex}
.main-nav a{font:500 13px "Montserrat",sans-serif;color:#333;text-decoration:none;margin-right:48px}
.main-nav a.active{color:var(--green)}
.nav-circle{top:67px;width:50px;height:50px;border:2px solid var(--green);border-radius:50%}
.nav-circle svg{position:absolute;left:13px;top:13px}

/* hero */
.hero{left:0;top:127px;width:1200px;height:517px;background:linear-gradient(90deg,#2a2a2a,#3a3a3a 50%,#2c2c2c)}
.hero-food{left:0;top:127px;width:465px;height:517px;background:linear-gradient(160deg,#c8644a 0,#9aab4a 45%,#4a5a2c 100%)}
.hero-mark{left:765px;top:205px;width:130px;height:130px;border-radius:50%;border:8px solid var(--green);background:rgba(140,198,63,.15)}
.hero-name{left:560px;top:360px;width:540px;text-align:center;font:600 64px "Montserrat",sans-serif;color:var(--green);letter-spacing:3px}
.hero-tag{left:500px;top:440px;width:660px;text-align:center;font:500 22px "Montserrat",sans-serif;color:var(--white)}
.btn{display:block;background:var(--green);color:var(--white);font:500 16px "Montserrat",sans-serif;text-align:center;border-radius:3px;text-decoration:none}
.hero-btn{left:757px;top:497px;width:141px;height:43px;line-height:43px}
.dots{left:568px;top:610px;display:flex;gap:8px}
.dots i{width:16px;height:16px;border:2px solid var(--white);border-radius:50%}
.dots i.on{border-color:var(--green)}

/* welcome */
.welcome{left:0;top:644px;width:1200px;height:214px;background:var(--green);text-align:center;color:var(--white)}
.welcome h2{margin-top:37px;font:500 25px "Montserrat",sans-serif}
.welcome hr{width:86px;margin:18px auto 0;border:0;border-top:3px solid var(--white)}
.welcome p{width:570px;margin:22px auto 0;font-size:12px;line-height:27px}

/* features */
.feature{top:905px;width:300px;text-align:center}
.feature-ring{margin:0 auto;width:146px;height:146px;border-radius:50%;border:5px solid var(--green);border-left-color:#d9ecbf;position:relative}
.feature-ring svg{position:absolute;left:36px;top:36px}
.feature h3{margin-top:30px;font:600 18px "Montserrat",sans-serif;color:var(--green);letter-spacing:.5px}
.feature p{margin-top:12px;font-size:12px;line-height:26px;color:var(--muted)}

/* featured products */
.featured{left:0;top:1233px;width:1200px;height:475px;background:var(--light);border-top:2px solid var(--green)}
.featured-tab{left:448px;top:1233px;width:327px;height:50px}
.featured-tab span{position:absolute;left:0;top:0;width:100%;line-height:50px;text-align:center;color:var(--white);font:500 21px "Montserrat",sans-serif}
.card{top:1325px;width:242px;height:335px;background:var(--white);border:1px solid var(--line);text-align:center}
.card-img{margin:8px;height:175px;border:1px solid var(--line)}
.card .price{margin-top:22px;font:500 22px "Montserrat",sans-serif;color:var(--green-dark)}
.card .name{margin-top:10px;font:500 14px "Montserrat",sans-serif;color:#333;letter-spacing:.5px}
.card-actions{margin-top:18px;display:flex;justify-content:center;gap:8px}
.card-actions i{width:33px;height:33px;border:1px solid #bbb;border-radius:50%;position:relative}
.card-actions svg{position:absolute;left:9px;top:9px}

/* snacks story */
.story-title{left:85px;top:1782px;font:600 22px "Montserrat",sans-serif;color:var(--green)}
.story-text{left:85px;width:545px;font-size:12px;line-height:27px;color:var(--muted)}
.story-btn{left:85px;top:2070px;width:127px;height:45px;line-height:45px;font-size:14px}
.story-pack{left:708px;top:1762px;width:365px;height:365px;border-radius:50%;background:linear-gradient(170deg,#cfad85 0,#a9825a 60%,#7e5b3b 100%)}

/* footer */
.site-footer{left:0;top:2185px;width:1200px;height:305px;background:linear-gradient(90deg,var(--wood-dark),var(--wood) 50%,var(--wood-dark))}
.foot-mark{left:145px;top:2212px;width:110px;height:110px;border-radius:50%;border:8px solid var(--green);background:rgba(140,198,63,.2)}
.foot-name{left:90px;top:2332px;width:220px;text-align:center;font:600 46px "Montserrat",sans-serif;color:var(--green);letter-spacing:2px}
.foot-col{color:var(--foot-text)}
.foot-col h4{font:600 17px "Montserrat",sans-serif;color:var(--white);margin-bottom:22px}
.contact-list{list-style:none;font-size:12px;line-height:16px;color:var(--foot-text)}
.contact-list li{display:flex;gap:14px;margin-bottom:12px}
.contact-list svg{flex:none;margin-top:1px}
.contact-list u{color:var(--foot-text)}
.foot-col p{font-size:12px;line-height:19px;color:var(--foot-text)}
.news-input{margin-top:18px;width:208px;height:34px;background:var(--white);color:#555;font-size:11px;line-height:34px;padding-left:14px}
.news-btn{margin-top:11px;width:80px;height:24px;line-height:24px;font-size:10px;border-radius:0}
.social{margin-top:20px;display:flex;gap:10px}
.social i{width:34px;height:34px;border:2px solid var(--white);border-radius:50%}
.foot-line{left:85px;top:2420px;width:1030px;border-top:1px solid #3d3d3d}
.copyright{left:0;top:2450px;width:1200px;text-align:center;font-size:12px;color:var(--foot-text)}
</style>
</head>
<body>

<header class="abs site-header">
  <div class="abs brand"><span class="brand-mark"></span><span class="brand-name">Brimora</span></div>
  <nav class="abs main-nav">
    <a class="active" href="#">HOME</a><a href="#">ABOUT US</a><a href="#">PRODUCTS</a><a href="#">NEWS</a><a href="#">GALLERY</a><a href="#" style="margin-right:0">CONTACT US</a>
  </nav>
  <div class="abs nav-circle" style="left:1010px">
    <svg width="20" height="20" viewBox="0 0 20 20" fill="#8cc63f"><path d="M1 2h3l3 10h9l2-7H6" fill="none" stroke="#8cc63f" stroke-width="2"/><circle cx="8" cy="16" r="2"/><circle cx="15" cy="16" r="2"/></svg>
  </div>
  <div class="abs nav-circle" style="left:1065px">
    <svg width="20" height="20" viewBox="0 0 20 20"><circle cx="8" cy="8" r="6" fill="none" stroke="#8cc63f" stroke-width="2.5"/><path d="M12.5 12.5L18 18" stroke="#8cc63f" stroke-width="3"/></svg>
  </div>
</header>
<div class="abs call-tab">
  <svg width="270" height="45" viewBox="0 0 270 45"><path d="M0 0H270L248 45H22Z" fill="#8cc63f"/></svg>
  <span>&#9990;&nbsp; CALL US : (000)-555-0182</span>
</div>

<section class="abs hero"></section>
<div class="abs hero-food" role="img" aria-label="Overhead photo of fresh food: salmon, peanuts, avocado, apples, beef and greens"></div>
<div class="abs hero-mark"></div>
<div class="abs hero-name">Brimora</div>
<div class="abs hero-tag">FUEL FOR THE BOLD TRAIL-WALKER &#8482;</div>
<a class="abs btn hero-btn" href="#">READ MORE</a>
<div class="abs dots"><i></i><i class="on"></i><i></i></div>

<section class="abs welcome">
  <h2>WELCOME TO BRIMORA FOODS</h2>
  <hr>
  <p>Our products are raw, organic, vegan, gluten-free, dairy-free, fiber-rich, nutrient-dense, antioxidant-rich real foods with no preservatives, no added sugar, and no artificial or plant-based sweeteners. And they are irresistibly scrumptious!</p>
</section>

<svg class="abs" style="left:38px;top:990px" width="24" height="120" viewBox="0 0 24 120"><path d="M22 2L2 60L22 118" fill="none" stroke="#ddd" stroke-width="2"/></svg>
<svg class="abs" style="left:1140px;top:990px" width="24" height="120" viewBox="0 0 24 120"><path d="M2 2L22 60L2 118" fill="none" stroke="#ddd" stroke-width="2"/></svg>

<div class="abs feature" style="left:107px">
  <div class="feature-ring"><svg width="64" height="64" viewBox="0 0 64 64" fill="#8cc63f"><circle cx="22" cy="38" r="18"/><circle cx="46" cy="34" r="14"/><path d="M18 18h8v6h-8zM43 16h6v6h-6z"/></svg></div>
  <h3>ORGANIC</h3>
  <p>Sed ut perspiciatis unde omnis iste natus error sit voluptatem accusantium doloremque laudantium, beatae vitae dicta sunt explicabo.</p>
</div>
<div class="abs feature" style="left:450px">
  <div class="feature-ring"><svg width="64" height="64" viewBox="0 0 64 64" fill="none" stroke="#8cc63f" stroke-width="3"><rect x="8" y="16" width="20" height="40" rx="4"/><path d="M12 16V8h12v8"/><path d="M28 56h30V40L44 28 28 40"/></svg></div>
  <h3>DAIRY-FREE</h3>
  <p>Sed ut perspiciatis unde omnis iste natus error sit voluptatem accusantium doloremque laudantium, beatae vitae dicta sunt explicabo.</p>
</div>
<div class="abs feature" style="left:795px">
  <div class="feature-ring"><svg width="64" height="64" viewBox="0 0 64 64" fill="#8cc63f"><path d="M8 58L52 10" stroke="#8cc63f" stroke-width="3"/><ellipse cx="46" cy="16" rx="5" ry="9" transform="rotate(45 46 16)"/><ellipse cx="36" cy="26" rx="5" ry="9" transform="rotate(45 36 26)"/><ellipse cx="26" cy="36" rx="5" ry="9" transform="rotate(45 26 36)"/><ellipse cx="40" cy="34" rx="5" ry="9" transform="rotate(-45 40 34)"/><ellipse cx="30" cy="44" rx="5" ry="9" transform="rotate(-45 30 44)"/></svg></div>
  <h3>GLUTEN-FREE</h3>
  <p>Sed ut perspiciatis unde omnis iste natus error sit voluptatem accusantium doloremque laudantium, beatae vitae dicta sunt explicabo.</p>
</div>

<section class="abs featured"></section>
<div class="abs featured-tab">
  <svg width="327" height="50" viewBox="0 0 327 50"><path d="M0 0H327C300 0 300 50 275 50H52C27 50 27 0 0 0Z" fill="#8cc63f"/></svg>
  <span>FEATURED PRODUCTS</span>
</div>

<div class="abs card" style="left:86px">
  <div class="card-img" role="img" aria-label="Chocolate bar pieces" style="background:linear-gradient(180deg,#f7f3f1 0,#e3d3cb 55%,#b89282 100%)"></div>
  <div class="price">$ 59.00</div><div class="name">CHOCOLATE</div>
  <div class="card-actions"><i><svg width="14" height="14"><rect x="2" y="3" width="10" height="8" fill="none" stroke="#999"/></svg></i><i><svg width="14" height="14"><path d="M7 12L2 6a3 3 0 015-3 3 3 0 015 3z" fill="none" stroke="#999"/></svg></i><i><svg width="14" height="14"><path d="M2 5h10M2 9h10" stroke="#999"/></svg></i></div>
</div>
<div class="abs card" style="left:348px">
  <div class="card-img" role="img" aria-label="Swirl of chocolate mousse" style="background:linear-gradient(180deg,#f8f5f4 0,#eddcd5 55%,#d2b0a3 100%)"></div>
  <div class="price">$ 59.00</div><div class="name">MOUSSE</div>
  <div class="card-actions"><i><svg width="14" height="14"><rect x="2" y="3" width="10" height="8" fill="none" stroke="#999"/></svg></i><i><svg width="14" height="14"><path d="M7 12L2 6a3 3 0 015-3 3 3 0 015 3z" fill="none" stroke="#999"/></svg></i><i><svg width="14" height="14"><path d="M2 5h10M2 9h10" stroke="#999"/></svg></i></div>
</div>
<div class="abs card" style="left:610px">
  <div class="card-img" role="img" aria-label="Ice cream sundae in a glass" style="background:linear-gradient(180deg,#f6f1ee 0,#e8dad0 55%,#c8ab98 100%)"></div>
  <div class="price">$ 59.00</div><div class="name">ICE CREAM</div>
  <div class="card-actions"><i><svg width="14" height="14"><rect x="2" y="3" width="10" height="8" fill="none" stroke="#999"/></svg></i><i><svg width="14" height="14"><path d="M7 12L2 6a3 3 0 015-3 3 3 0 015 3z" fill="none" stroke="#999"/></svg></i><i><svg width="14" height="14"><path d="M2 5h10M2 9h10" stroke="#999"/></svg></i></div>
</div>
<div class="abs card" style="left:872px">
  <div class="card-img" role="img" aria-label="Stack of square crackers" style="background:linear-gradient(180deg,#fbf7f1 0,#f3e1c6 55%,#e4bd86 100%)"></div>
  <div class="price">$ 59.00</div><div class="name">CRACKERS</div>
  <div class="card-actions"><i><svg width="14" height="14"><rect x="2" y="3" width="10" height="8" fill="none" stroke="#999"/></svg></i><i><svg width="14" height="14"><path d="M7 12L2 6a3 3 0 015-3 3 3 0 015 3z" fill="none" stroke="#999"/></svg></i><i><svg width="14" height="14"><path d="M2 5h10M2 9h10" stroke="#999"/></svg></i></div>
</div>

<h2 class="abs story-title">SELL NUTRITIOUS SNACKS</h2>
<p class="abs story-text" style="top:1830px">Sed ut perspiciatis unde omnis iste natus error sit voluptatem accusantium doloremque laudantium, totam rem aperiam, eaque ipsa quae ab illo inventore veritatis et quasi architecto beatae vitae dicta sunt explicabo. Nemo enim ipsam voluptatem quia voluptas sit aspernatur aut odit aut fugit, sed quia consequuntur magni dolores eos qui ratione voluptatem sequi nesciunt.</p>
<p class="abs story-text" style="top:1965px">Sed ut perspiciatis unde omnis iste natus error sit voluptatem accusantium doloremque laudantium, totam rem aperiam, eaque ipsa quae ab illo inventore veritatis et quasi architecto beatae vitae dicta sunt explicabo. Nemo enim ipsam voluptatem quia voluptas sit aspernatur</p>
<a class="abs btn story-btn" href="#">READ MORE</a>
<div class="abs story-pack" role="img" aria-label="Round Nuttaree® package lid with product label and chocolate ball"></div>

<footer class="abs site-footer"></footer>
<div class="abs foot-mark"></div>
<div class="abs foot-name">Brimora</div>

<div class="abs foot-col" style="left:405px;top:2222px;width:200px">
  <h4>CONTACT US</h4>
  <ul class="contact-list">
    <li><svg width="14" height="14" viewBox="0 0 14 14" fill="#e6e6e6"><path d="M2 4c0-2 2-3 5-3s5 1 5 3H9V3H5v1zM3 6h8l1 6H2z"/></svg>(000)-555-0182 &nbsp;(Phone)</li>
    <li><svg width="14" height="14" viewBox="0 0 14 14" fill="#e6e6e6"><rect x="3" y="1" width="8" height="4"/><rect x="1" y="5" width="12" height="6"/><rect x="3" y="9" width="8" height="4"/></svg>(000)-555-0182 &nbsp;&nbsp;&nbsp;(Fax)</li>
    <li><svg width="14" height="14" viewBox="0 0 14 14"><rect x="1" y="3" width="12" height="8" fill="none" stroke="#e6e6e6"/><path d="M1 3l6 5 6-5" fill="none" stroke="#e6e6e6"/></svg><u>hello@brimora.com</u></li>
    <li><svg width="14" height="14" viewBox="0 0 14 14" fill="#e6e6e6"><path d="M7 13S2 7 2 5a5 5 0 0110 0c0 2-5 8-5 8z"/><circle cx="7" cy="5" r="2" fill="#2b2b2b"/></svg><span># 2564 Lorem Ipsum Dummy<br>Lorem Ipsum Dummy</span></li>
  </ul>
</div>

<div class="abs foot-col" style="left:636px;top:2222px;width:220px">
  <h4>NEWSLETTER</h4>
  <p>Register Your email address to get information ablout us</p>
  <div class="news-input">Email Address</div>
  <a class="btn news-btn" href="#">SUBSCRIBE</a>
</div>

<div class="abs foot-col" style="left:902px;top:2222px;width:220px">
  <h4>FOLLOW US</h4>
  <p>Lorem ipsum dolor sit amet, conse ctetur adipiscing elit. Nulla in purus nibh. Donec ornare</p>
  <div class="social"><i></i><i></i><i></i><i></i><i></i></div>
</div>

<div class="abs foot-line"></div>
<div class="abs copyright">&copy; Copyright 2018 Brimora.All Rights Reserved</div>

</body>
</html>
```